Business cards for 3 Realtors at one brokerage

We will need a business card template that can be projected on 3 business cards. Harborline Realty & Investment Corp. has 3 realtors on staff Dane, Owen, and Miles. We all want a business card that shows our new logo and information. I will attach many versions of our Logo as well as head shots for each realtor (Owen- Long hair, youngest. Miles- Suit jacket, parted hair cut. Dane- Angled Pose, Shirt and Tie.) I have attached our information below.

Dane Foskett
801-555-0147
dane@harborlinehomesite.com
Principal Broker

Miles Tandrow
801-555-0162
miles@harborlinehomesite.com
Real Estate Agent

Owen Tandrow
801-555-0138
owen@harborlinehomesite.com
Real Estate Agent

Harborline Realty & Investment Corp.
HarborlineHomesite.com
5286 N 7200 Suite 208-617, South Jordan, UT 84009

Please feel free to reach out with any questions, comments, or concerns.

```html
<!DOCTYPE html>
<html lang="en">
<head>
<meta charset="utf-8">
<title>Harborline Realty – Business Cards</title>
<link href="https://fonts.googleapis.com/css2?family=Montserrat:wght@500;600;700&family=Arimo:wght@400&display=swap" rel="stylesheet">
<style>
  :root{
    --backdrop:#2b2b2b;
    --card-black:#050505;
    --card-grey:#3c3c3c;
    --brand-blue:#35a7f0;
    --logo-grey:#7d7d7d;
    --band-grey:#7a7a7a;
    --contact-row:#151515;
    --text-white:#ffffff;
    --url-grey:#9a9a9a;
    --photo-top:#4a4642;
    --photo-bottom:#d9d9d9;
  }
  *{margin:0;padding:0;box-sizing:border-box}
  html,body{width:1075px;height:1200px;overflow:hidden;background:var(--backdrop)}
  body{position:relative;font-family:'Arimo',Arial,sans-serif}

  .card{position:absolute;width:662px;height:395px;border-radius:22px;overflow:hidden;
    box-shadow:3px 4px 2px rgba(0,0,0,.55);
    background:linear-gradient(200deg,var(--card-grey) 0%,#141414 40%,var(--card-black) 70%)}
  .card--back{left:208px;top:187px}
  .card--front{left:205px;top:637px}

  .brand-circle{position:absolute;border:4px solid var(--brand-blue);border-radius:50%}
  .brand-name{position:absolute;left:0;right:0;text-align:center;font-family:'Montserrat',sans-serif;
    font-weight:600;color:var(--logo-grey);white-space:nowrap}
  .brand-tagline{position:absolute;left:0;right:0;text-align:center;font-family:'Montserrat',sans-serif;
    font-weight:600;color:var(--logo-grey);white-space:nowrap}

  /* back */
  .card--back .brand-circle{left:264px;top:94px;width:132px;height:132px}
  .card--back .brand-name{top:240px;font-size:33px;letter-spacing:.5px}
  .card--back .brand-tagline{top:285px;font-size:15px;letter-spacing:4.5px}
  .website{position:absolute;left:0;right:0;top:341px;text-align:center;font-size:18px;color:var(--url-grey)}
  .website b{font-weight:400;color:var(--brand-blue)}

  /* front */
  .front-brand{position:absolute;left:0;top:0;width:350px;height:232px}
  .card--front .brand-circle{left:123px;top:32px;width:106px;height:106px}
  .card--front .brand-name{top:150px;font-size:27px}
  .card--front .brand-tagline{top:184px;font-size:13px;letter-spacing:3.6px}

  .headshot{position:absolute;left:381px;top:0;width:281px;height:290px;
    background:linear-gradient(180deg,var(--photo-top) 0%,#6e6862 55%,var(--photo-bottom) 100%)}

  .name-band{position:absolute;left:0;top:232px;width:381px;height:58px;background:var(--band-grey)}
  .agent-name{position:absolute;left:32px;top:6px;font-family:'Montserrat',sans-serif;font-weight:700;
    font-size:22px;color:var(--brand-blue);white-space:nowrap}
  .agent-role{position:absolute;left:32px;top:33px;font-size:18px;color:var(--text-white);white-space:nowrap}

  .contact-row{position:absolute;left:0;top:290px;width:662px;height:57px;background:var(--contact-row);
    display:flex;align-items:center;padding-left:34px;gap:20px;color:var(--text-white);font-size:18px}
  .contact-item{display:flex;align-items:center;gap:8px}
  .address-bar{position:absolute;left:0;top:347px;width:662px;height:48px;background:var(--brand-blue);
    display:flex;align-items:center;padding-left:34px;gap:6px;color:var(--text-white);font-size:18px}
  .icon{fill:var(--brand-blue)}
  .icon--white{fill:var(--text-white)}
</style>
</head>
<body>

<section class="card card--back">
  <div class="brand-circle"></div>
  <div class="brand-name">HARBORLINE REALTY</div>
  <div class="brand-tagline">&amp; INVESTMENT CORP.</div>
  <div class="website">www.<b>HarborlineHomesite</b>.com</div>
</section>

<section class="card card--front">
  <div class="headshot" role="img" aria-label="Headshot photo of Owen Tandrow"></div>
  <div class="front-brand">
    <div class="brand-circle"></div>
    <div class="brand-name">HARBORLINE REALTY</div>
    <div class="brand-tagline">&amp; INVESTMENT CORP.</div>
  </div>
  <div class="name-band">
    <div class="agent-name">OWEN TANDROW</div>
    <div class="agent-role">Real Estate Agent</div>
  </div>
  <div class="contact-row">
    <span class="contact-item">
      <svg class="icon" width="20" height="20" viewBox="0 0 24 24"><path d="M6.6 10.8c1.4 2.8 3.8 5.1 6.6 6.6l2.2-2.2c.3-.3.7-.4 1-.2 1.1.4 2.3.6 3.6.6.6 0 1 .4 1 1V20c0 .6-.4 1-1 1C10.6 21 3 13.4 3 4c0-.6.4-1 1-1h3.5c.6 0 1 .4 1 1 0 1.3.2 2.5.6 3.6.1.3 0 .7-.2 1z"/></svg>
      801-555-0138
    </span>
    <span class="contact-item">
      <svg class="icon" width="22" height="16" viewBox="0 0 22 16"><path d="M0 0h22v16H0z M1.5 1.5 11 9l9.5-7.5" fill="none" stroke="#35a7f0" stroke-width="2"/><path d="M0 0h22L11 9z"/></svg>
      owen@harborlinehomesite.com
    </span>
  </div>
  <div class="address-bar">
    <svg class="icon--white" width="16" height="22" viewBox="0 0 16 22"><path d="M8 0C3.6 0 0 3.5 0 7.8 0 13.6 8 22 8 22s8-8.4 8-14.2C16 3.5 12.4 0 8 0zm0 10.6a2.8 2.8 0 1 1 0-5.6 2.8 2.8 0 0 1 0 5.6z"/></svg>
    5286 N 7200 Suite 208-617, South Jordan, UT 84009
  </div>
</section>

</body>
</html>
```